Organic Infographic – "The 4 Dimensions of Transformation"

Overview:
We are a coaching/education brand (Brackwater Institute) and need a redesigned infographic illustrating our 4-area transformation model. Our current version (attached) uses a rigid, hard-edged triangle/pyramid layout — we want a completely new visual approach that feels organic, soft, and alive, since the topic is human personal development, not a technical process.

Content structure (please keep the wording, redesign the visual form):

4 areas: "Embodiment – The Foundation" and "Focus & Intuition Redefined – The Lens" sit on the same base level. "Heart Centered Living – The Bridge" sits one level above, connecting/enabling the other two. "Becoming Unlimited – The Peak" sits at the top, made possible by Heart Centered Living.
The 4 areas influence and inspire one another — this mutual connection must be visually recognizable (e.g. through overlapping zones, blended color transitions, connecting flowing lines, or similar). Areas may stay visually distinct; the connection between them is what must be shown.
Hierarchy should be expressed mainly through position/arrangement (ascending flow), not through size differences — all 4 areas should carry similar visual weight, since each is equally essential.
A supporting element: "The Brackwater Methodology" with 3 phases (Phase 1: Awareness & Insight, Phase 2: Integration & Practice, Phase 3: Expansion & Sustainable Growth), each with a short description (text provided below).

Style direction:
Organic, soft, flowing shapes — no sharp angles or rigid geometric triangles. Attached are 3 moodboard references showing the direction we like: overlapping/blended circular shapes, flowing ribbon-style connections, and organic swirl divisions. Please don't copy any of them directly — combine this organic/overlapping visual language with our specific asymmetric hierarchy (2 areas base level + 1 bridge + 1 peak), which none of the references show exactly. This creative translation is the core task.

Icons: Please design one new, unified icon per area (4 total) plus 3 simple icons for the methodology phases — consistent style across all 7, your creative interpretation is welcome.

Typography: Headlines in Arsenal, body text in DM Sans.

Colors: Base palette — Embodiment D09176, Focus & Intuition Redefined B6623E, Heart Centered Living D9866B, Becoming Unlimited 6F7A70, dark text 23211A, light accent EACEC1. Slight adjustments are welcome if they improve visual distinction between areas.

Technical requirements (important):

Final files as vector format (SVG, AI, or EPS), with separated, editable, non-flattened/non-merged layers and paths.
Shapes should consist of simple, closed outline paths — no fine textures, no complex multi-stop gradients, no photorealistic rendering — since the artwork will later be manually redrawn as a whiteboard-animation video.
Primary format: 16:9 landscape. A secondary vertical/mobile version (3 outer areas stacked below the top area) is welcome but optional.

Usage rights: Full commercial usage across website, video, and social media required.

Attachments to include: current draft PDF (for text content and logo reference only — not for layout), our logo file, and the 3 moodboard reference images.

Budget: $100–150 — please let us know if this realistically allows for more designer participation, or advise on adjusting scope/budget

Methodology phase texts (for the 3 supporting icons):

Phase 1: Awareness & Insight
Cultivating self-reflection, identifying patterns, and gaining clarity on personal drivers through introspective practices and data-informed assessment.

Phase 2: Integration & Practice
Applying tools and frameworks, developing new habits, and aligning actions with core values through consistent application and feedback loops.

Phase 3: Expansion & Sustainable Growth
Achieving long-term transformation, exceeding limitations, and fostering resilience through continuous evolution and a purpose-driven approach.

```html
<!DOCTYPE html>
<html lang="en">
<head>
<meta charset="utf-8">
<title>The 4 Dimensions of Transformation – Brackwater Institute</title>
<link href="https://fonts.googleapis.com/css2?family=Arsenal:wght@400;700&family=DM+Sans:wght@400;500&family=Mr+Dafoe&display=swap" rel="stylesheet">
<style>
  :root{
    --page:#333333;
    --paper:#f5f1ea;
    --ink:#23211a;
    --sage:#7a8574;
    --sage-text:#7b8679;
    --sage-soft:#8a9384;
    --heart:#d4896b;
    --focus:#b8694a;
    --embody:#dba489;
    --rust:#b6623e;
    --accent:#eacec1;
    --sand:#ddd3b6;
    --white:#ffffff;
  }
  *{box-sizing:border-box;margin:0;padding:0}
  html,body{width:1200px;height:960px;overflow:hidden;background:var(--page)}
  .canvas{position:relative;width:1200px;height:960px}
  .slide{
    position:absolute;left:0;top:142px;width:1254px;height:706px;
    background:var(--paper);overflow:hidden;
    transform:scale(0.95694);transform-origin:0 0;
    font-family:"DM Sans",sans-serif;color:var(--ink);
  }

  /* decorations */
  .sun{position:absolute;left:1127px;top:-97px;width:160px;height:160px;border-radius:50%;background:var(--heart)}
  .dune{position:absolute;left:1075px;top:620px;width:230px;height:150px;border-radius:55% 45% 0 0/70% 60% 0 0;background:var(--sand)}
  .foliage{position:absolute;border-radius:50%;opacity:.45}
  .foliage--right{left:1112px;top:113px;width:142px;height:220px;background:radial-gradient(ellipse at 60% 40%,#a9ae98 0%,rgba(169,174,152,0) 70%)}
  .foliage--left{left:-10px;top:193px;width:95px;height:110px;background:radial-gradient(ellipse,#9a6a55 0%,rgba(154,106,85,0) 70%)}
  .foliage--corner{left:-20px;top:560px;width:230px;height:160px;background:radial-gradient(ellipse at 30% 70%,#c99a7e 0%,rgba(201,154,126,0) 70%)}
  .flourish{position:absolute;left:1080px;top:60px}

  /* dividers */
  .rule-v{position:absolute;left:623px;top:0;width:2px;height:566px;background:var(--rust)}
  .rule-h{position:absolute;left:522px;top:565px;width:732px;height:2px;background:var(--rust)}

  /* headline */
  .headline__the{position:absolute;left:44px;top:22px;font-family:"Mr Dafoe",cursive;font-size:62px;color:var(--sage);line-height:1;transform:rotate(-6deg)}
  .headline__num{position:absolute;left:82px;top:36px;font-family:"Arsenal",serif;font-weight:700;font-size:168px;line-height:1;color:var(--rust)}
  .headline__words{position:absolute;left:180px;top:84px;font-family:"Arsenal",serif;font-weight:700;font-size:47px;line-height:47px;color:var(--sage-text)}

  /* wheel */
  .wheel{position:absolute;left:68px;top:203px;width:460px;height:460px}
  .wheel__name{font-family:"Arsenal",serif;font-weight:700;font-size:20px;fill:var(--white)}
  .wheel__role{font-family:"DM Sans",sans-serif;font-size:11.5px;fill:var(--white)}

  /* methodology */
  .method__title{position:absolute;left:667px;top:36px;font-family:"Arsenal",serif;font-weight:700;font-size:37px;color:#33302a;white-space:nowrap}
  .method__title span{color:var(--sage-soft)}
  .phase{position:absolute;left:665px;width:430px}
  .phase__icon{position:absolute;left:0;top:0;width:60px;height:60px;border-radius:50%}
  .phase__icon i{position:absolute;left:16px;top:16px;width:28px;height:28px;border-radius:50%;background:rgba(255,255,255,.35)}
  .phase__icon--1{background:var(--sage)}
  .phase__icon--2{background:var(--heart)}
  .phase__icon--3{background:var(--focus)}
  .phase__body{position:absolute;left:74px;top:-9px;width:340px}
  .phase__num{font-family:"Arsenal",serif;font-weight:700;font-size:21px;line-height:24px;color:var(--rust)}
  .phase__name{font-family:"Arsenal",serif;font-weight:700;font-size:22px;line-height:25px;color:var(--sage-text);white-space:nowrap}
  .phase__text{margin-top:7px;font-size:13.4px;line-height:17px;color:var(--ink)}

  /* brand */
  .brand{position:absolute;left:673px;top:590px;display:flex;align-items:center;gap:11px}
  .brand__dot{width:66px;height:66px;border-radius:50%;background:#c97a5a}
  .brand__name{font-family:"Arsenal",serif;font-weight:400;font-size:37px;color:var(--sage-soft);white-space:nowrap}
</style>
</head>
<body>
<div class="canvas">
  <section class="slide">
    <div class="sun"></div>
    <div class="foliage foliage--right" role="img" aria-label="Sage green leafy branch"></div>
    <div class="foliage foliage--left" role="img" aria-label="Thin brown leaf sprig"></div>
    <div class="foliage foliage--corner" role="img" aria-label="Terracotta leaves over faint contour lines"></div>
    <div class="dune"></div>
    <svg class="flourish" width="160" height="60" viewBox="0 0 160 60" aria-hidden="true">
      <path d="M8 52 C40 48 70 30 100 22 S150 12 156 4" fill="none" stroke="#d9b9a6" stroke-width="1.2"/>
    </svg>

    <div class="rule-v"></div>
    <div class="rule-h"></div>

    <div class="headline__the">The</div>
    <div class="headline__num">4</div>
    <h1 class="headline__words">Dimensions<br>of Transformation</h1>

    <!-- wheel: two base areas side by side at the bottom, bridge and peak above -->
    <svg class="wheel" viewBox="-230 -230 460 460" aria-label="Four dimensions of transformation: Embodiment and Focus &amp; Intuition at the base, Heart Centered Living as the bridge, Becoming Unlimited as the peak">
      <defs>
        <path id="petal" d="M-212 -57 A220 220 0 0 1 57 -212 C70 -205 80 -185 85 -165 C95 -130 80 -75 36 -62 A72 72 0 0 0 -62 -36 C-75 -80 -130 -95 -165 -85 C-185 -80 -205 -70 -212 -57 Z"/>
        <radialGradient id="core" cx="45%" cy="40%" r="60%">
          <stop offset="0" stop-color="#ffffff"/>
          <stop offset="1" stop-color="#ece8e2"/>
        </radialGradient>
      </defs>
      <g transform="rotate(-15)" stroke="#f5f1ea" stroke-width="10" stroke-linejoin="round">
        <use href="#petal" fill="#7a8574"/>
        <use href="#petal" fill="#d4896b" transform="rotate(90)"/>
        <use href="#petal" fill="#b8694a" transform="rotate(180)"/>
        <use href="#petal" fill="#dba489" transform="rotate(270)"/>
      </g>
      <circle r="63" fill="url(#core)"/>

      <!-- Becoming Unlimited – The Peak -->
      <text class="wheel__name" text-anchor="end" x="-58" y="-148">Becoming</text>
      <text class="wheel__name" text-anchor="end" x="-58" y="-128">Unlimited</text>
      <text class="wheel__role" text-anchor="end" x="-58" y="-108">The Peak</text>
      <circle cx="-15" cy="-148" r="32" fill="#ffffff" stroke="#33302a" stroke-width="1.5"/>
      <circle cx="-15" cy="-148" r="18" fill="#e7e3dc" role="img" aria-label="Figure with a lightbulb idea icon"/>

      <!-- Heart Centered Living – The Bridge -->
      <text class="wheel__name" text-anchor="end" x="166" y="-120">Heart</text>
      <text class="wheel__name" text-anchor="end" x="166" y="-99">Centered</text>
      <text class="wheel__name" text-anchor="end" x="166" y="-78">Living</text>
      <text class="wheel__role" text-anchor="end" x="166" y="-59">The Bridge</text>
      <circle cx="150" cy="-8" r="31" fill="#ffffff"/>
      <circle cx="150" cy="-8" r="17" fill="#f3ddd3" role="img" aria-label="Radiant eye icon"/>

      <!-- Focus & Intuition – The Lens -->
      <text class="wheel__name" text-anchor="end" x="160" y="78">Focus &amp;</text>
      <text class="wheel__name" text-anchor="end" x="160" y="98">Intuition</text>
      <text class="wheel__role" text-anchor="end" x="160" y="115">The Lens</text>
      <circle cx="30" cy="151" r="31" fill="#ffffff"/>
      <circle cx="30" cy="151" r="17" fill="#f3ddd3" role="img" aria-label="Glowing standing figure icon"/>

      <!-- Embodiment – The Foundation -->
      <circle cx="-140" cy="32" r="31" fill="#ffffff"/>
      <circle cx="-140" cy="32" r="17" fill="#f6e3da" role="img" aria-label="Strong flexing figure icon"/>
      <text class="wheel__name" x="-182" y="96">Embodiment</text>
      <text class="wheel__role" x="-160" y="114">The Foundation</text>
    </svg>

    <h2 class="method__title">The Brackwater <span>Methodology</span></h2>

    <article class="phase" style="top:109px">
      <div class="phase__icon phase__icon--1" role="img" aria-label="Person with radiating lightbulb icon"><i></i></div>
      <div class="phase__body">
        <div class="phase__num">Phase 1</div>
        <div class="phase__name">Awareness &amp; Insight</div>
        <p class="phase__text">Cultivating self-reflection, identifying patterns and gaining clarity on personal drivers through introspective practices and data-informed assessment.</p>
      </div>
    </article>

    <article class="phase" style="top:263px">
      <div class="phase__icon phase__icon--2" role="img" aria-label="Interlocking gears icon"><i></i></div>
      <div class="phase__body">
        <div class="phase__num">Phase 2</div>
        <div class="phase__name">Integration &amp; Practice</div>
        <p class="phase__text">Applying tools and frameworks, developing new habits and aligning actions with core values through consistent application and feedback loops.</p>
      </div>
    </article>

    <article class="phase" style="top:405px">
      <div class="phase__icon phase__icon--3" role="img" aria-label="Globe held by hands icon"><i></i></div>
      <div class="phase__body">
        <div class="phase__num">Phase 3</div>
        <div class="phase__name">Expansion &amp; Sustainable Growth</div>
        <p class="phase__text">Achieving long-term transformation, exceeding limitations and fostering resilience through continuous evolution and a purpose-driven approach.</p>
      </div>
    </article>

    <div class="brand">
      <div class="brand__dot"></div>
      <div class="brand__name">Brackwater Institute</div>
    </div>
  </section>
</div>
</body>
</html>
```